Harborline Auto LLC

Car Dealer Customer Service
Address: 2874 Cresthaven Road, Shelbyville, TN 37162
web: www.harborlineautoxq.net
email: harborlineautoxq@mailnest.example
Phone: (931) 555-0148
Phone: (629) 555-0173

```html
<!DOCTYPE html>
<html lang="en">
<head>
<meta charset="utf-8">
<title>Harborline Auto – Business Card</title>
<link href="https://fonts.googleapis.com/css2?family=Arimo:wght@400;700&family=Exo+2:wght@800&family=Montserrat:wght@800&display=swap" rel="stylesheet">
<style>
  :root {
    --blue: #1f86bf;
    --blue-deep: #1a72a6;
    --gold: #ecb345;
    --white: #ffffff;
    --ink: #111111;
    --backdrop: #bdbdbd;
  }
  * { box-sizing: border-box; margin: 0; padding: 0; }
  html, body { width: 1200px; height: 800px; overflow: hidden; }
  body {
    background: var(--backdrop);
    position: relative;
    font-family: "Arimo", Arial, sans-serif;
  }
  .card {
    position: absolute;
    width: 525px;
    height: 300px;
    border-radius: 16px;
    overflow: hidden;
    border-bottom: 3px solid var(--gold);
  }
  .card-front { left: 40px; top: 110px; background: var(--white); }
  .card-back {
    left: 635px; top: 390px;
    background: linear-gradient(160deg, var(--blue) 0%, var(--blue-deep) 100%);
  }
  .front-shapes { position: absolute; inset: 0; }
  .holder { position: absolute; left: 34px; top: 52px; }
  .holder-name {
    font-family: "Montserrat", sans-serif;
    font-weight: 800; font-size: 21px; letter-spacing: 0.5px;
    color: var(--blue); text-transform: uppercase;
  }
  .holder-role { font-size: 14px; color: var(--gold); margin-top: 2px; }
  .contact-list {
    position: absolute; left: 34px; top: 124px;
    list-style: none; color: var(--white); font-size: 13.5px; line-height: 19px;
  }
  .contact-list li { display: flex; align-items: center; gap: 7px; }
  .contact-list svg { width: 12px; height: 12px; flex: none; }
  .address {
    position: absolute; left: 34px; top: 232px;
    font-size: 14.5px; line-height: 19px; color: var(--ink);
  }
  .front-mark {
    position: absolute; left: 318px; top: 60px; width: 170px; height: 140px;
    display: flex; flex-direction: column; align-items: center; justify-content: center; gap: 8px;
  }
  .mark-dot { width: 34px; height: 34px; border-radius: 50%; background: var(--gold); }
  .front-mark .brand-name {
    font-family: "Exo 2", sans-serif; font-weight: 800; font-size: 22px;
    color: var(--blue); text-transform: uppercase; text-align: center; line-height: 1.05;
  }
  .back-content {
    position: absolute; inset: 0;
    display: flex; flex-direction: column; align-items: center; justify-content: center; gap: 10px;
  }
  .back-dot { width: 62px; height: 62px; border-radius: 50%; background: var(--white); margin-bottom: 8px; }
  .back-content .brand-name {
    font-family: "Exo 2", sans-serif; font-weight: 800; font-size: 40px;
    color: var(--white); text-transform: uppercase; letter-spacing: 1px;
  }
  .tagline {
    font-family: "Exo 2", sans-serif; font-weight: 800; font-size: 22px;
    color: var(--gold); text-transform: uppercase; letter-spacing: 1.5px;
  }
</style>
</head>
<body>
  <section class="card card-front">
    <svg class="front-shapes" viewBox="0 0 525 300" aria-hidden="true">
      <rect x="432" y="30" width="93" height="72" fill="var(--gold)"/>
      <circle cx="403" cy="130" r="96" fill="var(--white)"/>
      <path d="M0 115 H330 A96 96 0 0 0 340 210 H0 Z" fill="var(--blue)"/>
    </svg>

    <div class="holder">
      <h1 class="holder-name">Marcus Ellery</h1>
      <p class="holder-role">Managing Director</p>
    </div>

    <ul class="contact-list">
      <li><svg viewBox="0 0 12 12"><path d="M2.5 1 L4.5 1 L5 3.5 L3.8 4.5 Q5 7 7.5 8.2 L8.5 7 L11 7.5 L11 9.5 Q10.5 11 9 11 Q1 10 1 3 Q1 1.5 2.5 1 Z" fill="var(--white)"/></svg>(931) 555-0148</li>
      <li><svg viewBox="0 0 12 12"><path d="M2.5 1 L4.5 1 L5 3.5 L3.8 4.5 Q5 7 7.5 8.2 L8.5 7 L11 7.5 L11 9.5 Q10.5 11 9 11 Q1 10 1 3 Q1 1.5 2.5 1 Z" fill="var(--white)"/></svg>(629) 555-0173</li>
      <li><svg viewBox="0 0 12 12"><circle cx="6" cy="6" r="5" fill="none" stroke="var(--white)" stroke-width="1.2"/><ellipse cx="6" cy="6" rx="2.2" ry="5" fill="none" stroke="var(--white)" stroke-width="1"/><path d="M1 6 H11" stroke="var(--white)" stroke-width="1"/></svg>www.harborlineautoxq.net</li>
      <li><svg viewBox="0 0 12 12"><rect x="0.5" y="2" width="11" height="8" fill="var(--white)"/><path d="M0.5 2 L6 6.5 L11.5 2" fill="none" stroke="var(--blue)" stroke-width="1"/></svg>harborlineautoxq@mailnest.example</li>
    </ul>

    <p class="address">2874 Cresthaven Road<br>Shelbyville, TN 37162</p>

    <div class="front-mark">
      <span class="mark-dot"></span>
      <span class="brand-name">Harborline<br>Auto</span>
    </div>
  </section>

  <section class="card card-back">
    <div class="back-content">
      <span class="back-dot"></span>
      <h2 class="brand-name">Harborline Auto</h2>
      <p class="tagline">Car Dealer Customer Service</p>
    </div>
  </section>
</body>
</html>
```